Quillfern Vaults - Direct Mailer / Flyer

We are excited to announce the launch of our new company, Quillfern Vaults, a premier cohosting facility and data center dedicated to Cryptocurrency Miners. Our website, https://quillfernvaults.example, provides detailed information about our offerings and showcases the innovative design schemes for the entire project.

Quillfern Vaults stands out in the industry by offering both GPU Hosting and ASIC Hosting services in our state-of-the-art facility, equipped with an impressive 17 Megawatts of available power. What sets us apart is our unique billing system based on actual metered power usage. We charge $0.08 for ASIC miners and $0.09 for GPU miners, ensuring cost-effectiveness and transparency for our clients.

Our commitment to excellence is evident in our use of cutting-edge technology, top-notch facilities, and strategic partnerships. These elements come together to deliver exceptional solutions tailored for real-world applications in the cryptocurrency space.

As part of our promotional efforts, we are developing a direct mailer/flyer to introduce Quillfern Vaults to a wider audience. This promotional material will also serve as a handout at events, to potential customers, and more. We welcome creative ideas and suggestions to maximize the versatility of this design and reach diverse target audiences effectively.

For a comprehensive overview of our services and to explore our design concepts, please visit https://quillfernvaults.example. Quillfern Vaults is poised to revolutionize the mining industry, and we look forward to partnering with you for success in the digital currency era.

```html
<!DOCTYPE html>
<html lang="en">
<head>
<meta charset="utf-8">
<title>Quillfern Vaults – Flyer</title>
<link href="https://fonts.googleapis.com/css2?family=Saira+Semi+Condensed:wght@600;700&family=Barlow:wght@400;500;600;700&display=swap" rel="stylesheet">
<style>
:root{
  --stage:#3b3b3d;
  --blue:#1f3ea8;
  --yellow:#f3d20b;
  --card:#e5e9f6;
  --card-green:#e3f1ea;
  --green:#1f8a45;
  --ink:#111;
  --white:#fff;
  --soft:#d9def0;
}
*{margin:0;padding:0;box-sizing:border-box}
html,body{width:1200px;height:800px;overflow:hidden}
body{background:var(--stage);font-family:"Barlow",sans-serif;position:relative}
.flyer{position:absolute;left:330px;top:19px;width:540px;height:762px;background:#f3f4f7;overflow:hidden}
.hero{position:absolute;left:0;top:0;width:540px;height:282px;background:var(--blue)}
.hero-pattern{position:absolute;left:282px;top:0;width:258px;height:282px;background:linear-gradient(135deg,#2a4bb8,#22409f 60%,#1e3a9c)}
.logo-tab{position:absolute;left:0;top:0}
.brand{position:absolute;left:20px;top:22px;display:flex;align-items:center;gap:7px;font-family:"Saira Semi Condensed",sans-serif;font-weight:700;font-size:18px;line-height:18px;color:var(--ink);letter-spacing:.3px;text-transform:uppercase;white-space:nowrap}
.brand-mark{width:20px;height:16px;background:var(--ink)}
.headline{position:absolute;left:20px;top:66px;font-family:"Saira Semi Condensed",sans-serif;font-weight:700;font-size:35px;line-height:40px;color:var(--white);white-space:nowrap}
.rule{position:absolute;left:24px;top:197px;width:109px;height:2px;background:var(--yellow)}
.tagline{position:absolute;left:24px;top:209px;width:170px;font-size:11px;line-height:13px;color:var(--soft)}
.pill{position:absolute;height:24px;background:var(--yellow);border-radius:3px;display:flex;align-items:center;gap:4px;padding:0 6px;font-weight:600;font-size:10.5px;color:var(--blue);white-space:nowrap}
.pill svg{width:13px;height:13px;flex:none}
.service{position:absolute;top:302px;width:117px;height:131px;background:var(--card);border-radius:8px;padding:18px 10px 0 11px}
.service svg{width:20px;height:20px}
.service h3{margin-top:20px;font-size:11px;font-weight:700;color:var(--blue);white-space:nowrap}
.service p{margin-top:7px;font-size:6.4px;line-height:8.6px;color:#333}
.tag{position:absolute;top:296px;height:11px;border-radius:2px;font-size:4.8px;font-weight:700;display:flex;align-items:center;justify-content:center}
.tag-popular{left:206px;width:44px;background:var(--yellow);color:var(--ink)}
.tag-value{left:471px;width:38px;background:var(--green);color:var(--white)}
.solutions-title{position:absolute;left:20px;top:458px;font-family:"Saira Semi Condensed",sans-serif;font-weight:700;font-size:21px;line-height:27px;color:var(--ink);text-transform:uppercase;white-space:nowrap}
.solutions-copy{position:absolute;left:20px;top:521px;width:245px;font-size:6px;line-height:7.6px;color:#222}
.stat{position:absolute;top:450px;width:93px;height:104px;border-radius:8px;padding:14px 11px 0}
.stat svg{width:22px;height:22px}
.stat strong{display:block;margin-top:14px;font-size:12.5px;font-weight:700}
.stat span{display:block;margin-top:2px;font-size:8.6px;line-height:10.3px}
.stat-power{left:294px;background:var(--card);color:var(--blue)}
.stat-green{left:418px;background:var(--card-green);color:var(--green)}
.features{position:absolute;left:0;top:564px;width:540px;height:162px;background:var(--yellow)}
.features h2{position:absolute;left:22px;top:9px;font-family:"Saira Semi Condensed",sans-serif;font-weight:700;font-size:21px;line-height:24px;color:var(--ink);text-transform:uppercase;white-space:nowrap}
.feature{position:absolute;height:48px;background:var(--ink);border-radius:4px;padding:6px 7px 0;overflow:hidden}
.feature h4{display:flex;align-items:center;gap:4px;font-size:10.5px;line-height:13px;font-weight:500;color:var(--white);white-space:nowrap}
.feature h4 svg{width:12px;height:12px;flex:none}
.feature p{margin-top:3px;font-size:5.2px;line-height:6.5px;color:var(--yellow)}
.footer{position:absolute;left:0;top:726px;width:540px;height:36px;background:var(--blue);display:flex;align-items:center;justify-content:center;font-size:14px;font-weight:600;letter-spacing:2px;color:var(--white)}
</style>
</head>
<body>
<main class="flyer">
  <section class="hero">
    <div class="hero-pattern" role="img" aria-label="Faint circuit-line pattern with one bright white trace"></div>
    <svg class="logo-tab" width="260" height="58" viewBox="0 0 260 58"><polygon points="0,0 256,0 240,56 0,56" fill="#fff"/></svg>
    <div class="brand"><span class="brand-mark"></span>Quillfern Vaults</div>
    <h1 class="headline">Transform<br>Mining With<br>Cohosting</h1>
    <div class="rule"></div>
    <p class="tagline">Miners deserve the best - choose the hosting company that delivers excellence!</p>

    <div class="pill" style="left:319px;top:54px"><svg viewBox="0 0 16 16" fill="none" stroke="currentColor" stroke-width="1.6"><path d="M8 1.5l5.5 2v4c0 3.5-2.5 6-5.5 7-3-1-5.5-3.5-5.5-7v-4z"/><path d="M5.5 8l2 2 3-3.5"/></svg>New Secure Facility</div>
    <div class="pill" style="left:415px;top:106px"><svg viewBox="0 0 16 16" fill="none" stroke="currentColor" stroke-width="1.6"><path d="M2 12a6 6 0 1 1 12 0z"/><path d="M8 11l3-4"/></svg>Speedy Support</div>
    <div class="pill" style="left:286px;top:150px"><svg viewBox="0 0 16 16" fill="none" stroke="currentColor" stroke-width="1.6"><path d="M6 10l-3 3M9 13l4-4 1-7-7 1-4 4 2 2M10 6h0"/></svg>99.45% Uptime</div>
    <div class="pill" style="left:389px;top:192px"><svg viewBox="0 0 16 16" fill="none" stroke="currentColor" stroke-width="1.6"><path d="M4 11a3 3 0 0 1 0-6 4 4 0 0 1 8 1 2.5 2.5 0 0 1 0 5z"/><path d="M6 14h0M8 13h0M10 14h0"/></svg>24/7 Remote Access</div>
  </section>

  <article class="service" style="left:20px">
    <svg viewBox="0 0 24 24" fill="none" stroke="#1f3ea8" stroke-width="1.8"><rect x="2" y="9" width="20" height="7" rx="1" transform="rotate(-40 12 12)"/><circle cx="9" cy="14" r="1.5"/><circle cx="13" cy="11" r="1.5"/></svg>
    <h3>GPU Hosting</h3>
    <p>Begin your GPU Hosting journey with rates starting at $0.09 kWh, accepting all equipment.</p>
  </article>
  <article class="service" style="left:150px">
    <svg viewBox="0 0 24 24" fill="none" stroke="#1f3ea8" stroke-width="1.8"><rect x="6" y="6" width="12" height="12"/><rect x="9.5" y="9.5" width="5" height="5"/><path d="M9 2v4M15 2v4M9 18v4M15 18v4M2 9h4M2 15h4M18 9h4M18 15h4"/></svg>
    <h3>ASIC Hosting</h3>
    <p>Get your ASICs directly from us or send yours in today, starting at an all-in rate of $0.08 kWh.</p>
  </article>
  <article class="service" style="left:279px">
    <svg viewBox="0 0 24 24" fill="none" stroke="#1f3ea8" stroke-width="1.8"><circle cx="12" cy="12" r="8"/><circle cx="12" cy="12" r="3"/><path d="M3 3l4 4M21 3l-4 4M3 21l4-4M21 21l-4-4"/></svg>
    <h3>Mining Hardware</h3>
    <p>Looking for mining hardware? Our equipment comes with no additional markup, ever.</p>
  </article>
  <article class="service" style="left:408px">
    <svg viewBox="0 0 24 24" fill="none" stroke="#1f3ea8" stroke-width="1.8"><rect x="5" y="2" width="14" height="20" rx="1"/><path d="M8 6h8M8 9h8M8 17l3-3 2 2 3-3"/></svg>
    <h3>Crypto Consulting</h3>
    <p>Enjoy complete White Glove Services for setup, insurance, and tax consulting.</p>
  </article>
  <div class="tag tag-popular">MOST POPULAR</div>
  <div class="tag tag-value">BEST VALUE</div>

  <h2 class="solutions-title">Real Solutions For<br>Real Applications</h2>
  <p class="solutions-copy">Quillfern Vaults has committed to leveraging cutting-edge technology, state-of-the-art facilities, and strategic partnerships to deliver exceptional solutions tailored for real-world applications in the cryptocurrency space.</p>

  <div class="stat stat-power">
    <svg viewBox="0 0 24 24" fill="none" stroke="currentColor" stroke-width="1.8"><rect x="2" y="3" width="8" height="8"/><rect x="14" y="2" width="8" height="5"/><rect x="14" y="10" width="8" height="5"/><rect x="14" y="18" width="8" height="4"/><path d="M10 7h4M10 12h4M6 11v9h8"/></svg>
    <strong>4,000,000+</strong><span>watts available<br>for hosting</span>
  </div>
  <div class="stat stat-green">
    <svg viewBox="0 0 24 24" fill="none" stroke="currentColor" stroke-width="1.8"><circle cx="11" cy="11" r="8"/><path d="M3 11h16M11 3c3 3 3 13 0 16M11 3c-3 3-3 13 0 16"/><circle cx="19" cy="19" r="2.2" fill="#e3f1ea"/></svg>
    <strong>2,000,000+</strong><span>watts of green<br>energy being<br>produced</span>
  </div>

  <section class="features">
    <h2>Hosting Tailored To Your Needs</h2>
    <div class="feature" style="left:23px;top:41px;width:130px">
      <h4><svg viewBox="0 0 16 16" fill="none" stroke="#fff" stroke-width="1.4"><path d="M9 1L3 9h4l-1 6 6-8H8z"/></svg>99.45% Uptime</h4>
      <p>We boast an impressive uptime of 99.45% on average, ensuring consistent availability and reliability for users.</p>
    </div>
    <div class="feature" style="left:184px;top:41px;width:130px">
      <h4><svg viewBox="0 0 16 16" fill="none" stroke="#fff" stroke-width="1.4"><rect x="2" y="2" width="7" height="12"/><path d="M4 5h3M4 8h3M9 10h5v4H9"/></svg>Advanced Security</h4>
      <p>Employing advanced security measures for protection against potential threats and unauthorized access.</p>
    </div>
    <div class="feature" style="left:356px;top:41px;width:146px">
      <h4><svg viewBox="0 0 16 16" fill="none" stroke="#fff" stroke-width="1.4"><path d="M2 14h12M3 14V7h4v7M9 14V3h4v11M5 9h0M11 5h0"/></svg>Large Facility Capacity</h4>
      <p>Our 4MW facility capacity underscores the infrastructure's ability to accommodate high-energy demands.</p>
    </div>
    <div class="feature" style="left:23px;top:100px;width:130px">
      <h4><svg viewBox="0 0 16 16" fill="none" stroke="#fff" stroke-width="1.4"><path d="M3 9V7a5 5 0 0 1 10 0v2M2 9h2v4H2zM12 9h2v4h-2zM13 13c0 1.5-2 2-4 2"/></svg>Expert Support</h4>
      <p>Benefit from expert support, ensuring assistance and guidance to optimize equipment and resolve issues effectively.</p>
    </div>
    <div class="feature" style="left:184px;top:100px;width:130px">
      <h4><svg viewBox="0 0 16 16" fill="none" stroke="#fff" stroke-width="1.4"><circle cx="8" cy="8" r="6"/><path d="M8 8l3-3M5 11h6"/></svg>Metered Usage</h4>
      <p>We exclusively bill you based on your usage, without exceptions! Leveraging state-of-the-art metering.</p>
    </div>
    <div class="feature" style="left:356px;top:100px;width:146px">
      <h4><svg viewBox="0 0 16 16" fill="none" stroke="#fff" stroke-width="1.4"><circle cx="7" cy="5" r="3"/><path d="M2 14c0-3 2-5 5-5M10 12h4M12 10v4"/></svg>Direct Equipment Access</h4>
      <p>Effectively command your operations with a comprehensive, full-spectrum control system - you got the keys.</p>
    </div>
  </section>

  <footer class="footer">www.quillfernvaults.example</footer>
</main>
</body>
</html>
```